Young, dynamic furniture company needs a new business card design

We require a new business card design for our modern furniture company which supplies furniture and appliances to the property and development market.
Oakridge Interiors has become one of the leading furniture & appliance suppliers to the property market withing London. With over 10 years experience, we have increased our business to supply not only private landlords and managing agents, but also property developers, housing associations and local councils.
We offer not only a complete range of furniture which includes beds, wardrobes, dining sets and sofas, but also a high quality, full delivery and assembly service to help you with all our furnishing needs.

Target Market(s)

Private landlords, estate agents, letting agents, property management companies

Industry/Entity Type

Business

Contact Information for Business Card

Name,
Title,
Address,
Mobile,
Telephone,
Fax, Website, email address

Font styles to use
Sans Serif

Colors
3176b5
0555a3
85abd2
cfdeed

Requirements
Must have
• All the above information for each of our staff, along with our logo

```html
<!DOCTYPE html>
<html lang="en">
<head>
<meta charset="utf-8">
<title>Oakridge Interiors – Business Card</title>
<link href="https://fonts.googleapis.com/css2?family=Montserrat:wght@400;700&family=Roboto+Condensed:wght@400&display=swap" rel="stylesheet">
<style>
  :root {
    --stage: #2a2a2c;
    --front-navy: #27326f;
    --panel-navy: #1f3a6f;
    --ink: #1f1f22;
    --paper: #ffffff;
    --brand-blue: #3176b5;
  }
  * { box-sizing: border-box; margin: 0; padding: 0; }
  html, body { width: 1189px; height: 1200px; overflow: hidden; }
  body { background: var(--stage); position: relative; font-family: "Montserrat", sans-serif; }

  .card {
    position: absolute;
    left: 171px;
    width: 855px;
    height: 488px;
    box-shadow: 0 6px 18px rgba(0,0,0,0.5);
  }
  .card--front { top: 67px; background: var(--front-navy); }
  .card--back  { top: 626px; background: var(--paper); }

  .brand {
    position: absolute;
    left: 0; right: 0;
    text-align: center;
    font-family: "Roboto Condensed", sans-serif;
    font-weight: 400;
  }
  .brand__row { display: inline-flex; align-items: center; gap: 14px; }
  .brand__square { width: 30px; height: 30px; background: var(--brand-blue); }
  .brand__name { font-size: 36px; letter-spacing: 0.5px; line-height: 1; }
  .brand__tagline { font-size: 19px; margin-top: 8px; letter-spacing: 0.3px; }

  .card--front .brand { top: 206px; color: var(--paper); }
  .card--back .brand { top: 205px; width: 421px; right: auto; color: var(--ink); }
  .card--back .brand__name { font-size: 33px; }
  .card--back .brand__tagline { font-size: 17px; }

  .divider { position: absolute; left: 421px; top: 0; width: 3px; height: 100%; background: var(--ink); }

  .details {
    position: absolute;
    left: 429px; top: 0; right: 0; bottom: 0;
    background: var(--panel-navy);
    color: var(--paper);
    padding: 76px 0 0 39px;
  }
  .details__name { font-size: 29px; font-weight: 700; line-height: 1; letter-spacing: 0.3px; }
  .details__title { font-size: 20px; line-height: 1.1; }
  .details__address { margin-top: 62px; font-size: 20px; line-height: 31px; }
  .contacts { list-style: none; margin-top: 12px; }
  .contacts li { display: flex; align-items: center; gap: 10px; font-size: 20px; height: 30.5px; }
  .contacts svg { width: 26px; height: 26px; flex: none; }
</style>
</head>
<body>

<section class="card card--front">
  <div class="brand">
    <div class="brand__row"><span class="brand__square"></span><span class="brand__name">OAKRIDGE INTERIORS</span></div>
    <div class="brand__tagline">TRADE FURNITURE SOLUTIONS</div>
  </div>
</section>

<section class="card card--back">
  <div class="brand">
    <div class="brand__row"><span class="brand__square"></span><span class="brand__name">OAKRIDGE INTERIORS</span></div>
    <div class="brand__tagline">TRADE FURNITURE SOLUTIONS</div>
  </div>
  <div class="divider"></div>
  <div class="details">
    <div class="details__name">DANIEL HART</div>
    <div class="details__title">Manager</div>
    <div class="details__address">Your Address,2nd Ste<br>Millbrook, Texas 1234, USA</div>
    <ul class="contacts">
      <li><svg viewBox="0 0 26 26"><rect width="26" height="26" fill="#fff"/><path d="M8 5c-2 1-2 4 0 8s5 7 8 8c2 0 3-1 3-2l-3-3-2 1c-2-1-3-3-4-5l1-2-3-4z" fill="#1f3a6f"/></svg>123 456 7890</li>
      <li><svg viewBox="0 0 26 26"><rect width="26" height="26" fill="#fff"/><rect x="8" y="5" width="10" height="5" fill="#1f3a6f"/><rect x="5" y="10" width="16" height="8" fill="#1f3a6f"/><rect x="8" y="16" width="10" height="5" fill="#fff" stroke="#1f3a6f" stroke-width="1.5"/></svg>123 456 7890</li>
      <li><svg viewBox="0 0 26 26"><rect width="26" height="26" fill="#fff"/><rect x="8" y="4" width="10" height="18" rx="2" fill="#1f3a6f"/><rect x="10" y="7" width="6" height="6" fill="#fff"/></svg>123 456 7890</li>
      <li><svg viewBox="0 0 26 26"><rect width="26" height="26" fill="#fff"/><rect x="4" y="7" width="18" height="12" fill="#1f3a6f"/><path d="M4 7l9 7 9-7" fill="none" stroke="#fff" stroke-width="1.5"/></svg>your@yourcompany.com</li>
      <li><svg viewBox="0 0 26 26"><rect width="26" height="26" fill="#fff"/><g fill="none" stroke="#1f3a6f" stroke-width="1.5"><circle cx="13" cy="13" r="8"/><ellipse cx="13" cy="13" rx="3.5" ry="8"/><path d="M5 13h16M6.5 9h13M6.5 17h13"/></g></svg>www.yourcompany.com</li>
    </ul>
  </div>
</section>

</body>
</html>
```